Harborview Estates Business Card for Apartment Buildings

Create business cards for resident managers who run apartment buildings. The audience is the public who are searching for apartment rentals, and current residents who live at the apartment building. Key design element will be incorporating the company logo, however, the logo cannot dominate. The building name and manager name are more important than the logo. Current business card design leaves little room for copy, so we may need to reduce the size on the current card to allow for more space for copy.

Target Market(s)

Adults 18-65 years of age, who are looking for an apartment rental, plus current residents who live at our apartment buildings.

Industry/Entity Type

Property Management

Contact Information for Business Card

A major design element will be use of the company logo. Important property and manager contact information must be part of the design. The size of the logo will need to be reduced to make room for building and manager contact copy.

Font styles to use
Sans Serif

Colors
3176b5
000000
959595
ffffff

Requirements
Must have
• 1) Incorporate the company logo.
• 2) Use the company colors (dark blue, black/grey, over white).
• 3) FEATURE THE BUILDING NAME
• 4) FEATURE THE MANAGER NAME
• 5) The company name is less important than BUILDING and MANAGER
• 6) Manager contact information
• **SEE ATTACHED CREATIVE BRIEF**
Nice to have
• 1) Back of card logo watermark
• 2) Ability to write notes on back of carfd
Should not have
• Avoid letting the company logo dominate the card, the building name and manager are more important than the company logo.

```html
<!DOCTYPE html>
<html lang="en">
<head>
<meta charset="utf-8">
<title>Harborview Estates – Resident Manager Card</title>
<link href="https://fonts.googleapis.com/css2?family=Roboto:wght@400;500;700&display=swap" rel="stylesheet">
<style>
  :root {
    --brand-blue: #0f67a8;
    --ink-grey: #4a4a4a;
    --text-grey: #555555;
    --rule-grey: #333333;
    --band-grey: #4b4c4e;
    --paper: #ffffff;
    --backdrop: #e9e9e9;
    --watermark: #e6e8ef;
  }
  * { box-sizing: border-box; margin: 0; padding: 0; }
  html, body { width: 1200px; height: 960px; overflow: hidden; }
  body {
    background: var(--backdrop);
    font-family: "Roboto", Arial, sans-serif;
    position: relative;
  }
  .card {
    position: absolute;
    left: 245px;
    width: 711px;
    height: 406px;
    background: var(--paper);
    box-shadow: 0 2px 6px rgba(0,0,0,0.18);
    overflow: hidden;
  }
  .card--front { top: 40px; }
  .card--back { top: 500px; }

  .company-mark {
    position: absolute;
    right: 38px;
    top: 74px;
    display: flex;
    align-items: center;
    gap: 12px;
    color: var(--brand-blue);
    font-weight: 700;
  }
  .company-mark__dot {
    width: 26px; height: 26px;
    border-radius: 50%;
    background: var(--brand-blue);
  }
  .company-mark__name { font-size: 28px; letter-spacing: 0.5px; line-height: 1; }

  .manager { position: absolute; left: 48px; top: 152px; }
  .manager__name { color: var(--brand-blue); font-size: 22px; font-weight: 700; }
  .manager__title { color: var(--text-grey); font-size: 16px; margin-top: 4px; }

  .divider {
    position: absolute;
    left: 50px; right: 0; top: 224px;
    height: 1.5px;
    background: var(--rule-grey);
  }

  .contacts { position: absolute; left: 46px; top: 250px; list-style: none; }
  .contacts li {
    display: flex; align-items: center; gap: 8px;
    height: 24px;
    color: var(--text-grey); font-size: 15.5px;
  }
  .contacts svg { width: 18px; height: 18px; fill: var(--brand-blue); }

  .property { position: absolute; left: 480px; top: 274px; font-size: 15.5px; line-height: 24px; color: var(--text-grey); }
  .property__name { color: var(--brand-blue); font-weight: 700; }

  .footer-band { position: absolute; left: 0; top: 370px; width: 711px; height: 36px; }
  .website {
    position: absolute; left: 480px; top: 377px;
    color: var(--paper); font-size: 15.5px;
  }

  .back-mark {
    position: absolute; left: 0; right: 0; top: 0; bottom: 0;
    display: flex; align-items: center; justify-content: center; gap: 20px;
    color: var(--watermark); font-weight: 700;
  }
  .back-mark__dot { width: 70px; height: 70px; border-radius: 50%; background: var(--watermark); }
  .back-mark__name { font-size: 52px; letter-spacing: 1px; }
</style>
</head>
<body>
  <section class="card card--front" aria-label="Business card front">
    <div class="company-mark">
      <span class="company-mark__dot"></span>
      <span class="company-mark__name">HARBORVIEW ESTATES</span>
    </div>

    <div class="manager">
      <h1 class="manager__name">Marisol Vega</h1>
      <p class="manager__title">Resident Manager</p>
    </div>

    <div class="divider"></div>

    <ul class="contacts">
      <li>
        <svg viewBox="0 0 20 20" aria-hidden="true"><path d="M6 2c1 0 2 3 2 4s-2 1-2 2c0 2 2 5 4 6 1 0 1-2 2-2s4 1 4 2-1 3-3 3C7 17 3 10 3 6c0-2 2-4 3-4z"/></svg>
        555-210-4471
      </li>
      <li>
        <svg viewBox="0 0 20 20" aria-hidden="true"><path d="M5 2h10v5H5z M2 8h16v7h-3v3H5v-3H2z M7 13v3h6v-3z" fill-rule="evenodd"/></svg>
        555-210-4488
      </li>
      <li>
        <svg viewBox="0 0 20 20" aria-hidden="true"><path d="M6 1h8a1 1 0 0 1 1 1v16a1 1 0 0 1-1 1H6a1 1 0 0 1-1-1V2a1 1 0 0 1 1-1zm1 2v11h6V3zm3 12.5a1 1 0 1 0 0 2 1 1 0 0 0 0-2z" fill-rule="evenodd"/></svg>
        555-384-9025
      </li>
      <li>
        <svg viewBox="0 0 20 20" aria-hidden="true"><path d="M2 5h16v10H2z M3 6l7 5 7-5" /><path d="M3 6l7 5 7-5" stroke="#fff" stroke-width="1.2" fill="none"/></svg>
        marisol@harborviewest.com
      </li>
    </ul>

    <address class="property" style="font-style:normal">
      <div class="property__name">Linden Court Apartments</div>
      <div>2145 Meridian Avenue</div>
      <div>Lakeport, CA 95453</div>
    </address>

    <svg class="footer-band" viewBox="0 0 711 36" aria-hidden="true">
      <polygon points="0,5 452,5 440,17 0,17" fill="var(--band-grey)"/>
      <rect x="0" y="23" width="711" height="10" fill="var(--brand-blue)"/>
      <polygon points="465,0 711,0 711,33 446,33" fill="var(--brand-blue)"/>
      <line x1="465" y1="0" x2="446" y2="23" stroke="#fff" stroke-width="3"/>
    </svg>
    <span class="website">www.harborviewest.com</span>
  </section>

  <section class="card card--back" aria-label="Business card back">
    <div class="back-mark">
      <span class="back-mark__dot"></span>
      <span class="back-mark__name">HARBORVIEW ESTATES</span>
    </div>
  </section>
</body>
</html>
```